Design a large parking banner – mandatory ticket validation in the shop

Banner Size:
548 cm (width) x 154 cm (height)
Note: The banner will be placed in a metal frame at our parking lot entrance, fully visible to every incoming truck driver. The message must be easy to read from a distance.
Goal of the Banner:
To inform all truck drivers that they must validate their entry ticket inside the shop, even if they are parking for a short time.
The message must be displayed in multiple languages for international drivers.
Mandatory Content:
Main message – in multiple languages (clearly separated or stacked):
Dutch (NL): Vergeet je ticket niet te valideren in de shop – verplicht, ook bij kort parkeren!
French (FR): N'oubliez pas de valider votre ticket à la boutique – obligatoire, même pour un court arrêt !
English (EN): Don't forget to validate your entry ticket in the shop – mandatory, even for short stops!
German (DE): Vergessen Sie nicht, Ihr Einfahrticket im Shop zu entwerten – Pflicht, auch bei kurzem Parken!
Polish (PL): Nie zapomnij zatwierdzić biletu w sklepie – obowiązkowe, nawet przy krótkim postoju!
Romanian (RO): Nu uitați să validați biletul în magazin – obligatoriu, chiar și pentru opriri scurte!
You can include more languages if space allows, but these are essential.
Opening Hours Block (in one section below):
Shop Opening Hours
Mon – Fri: 05:30 – 22:00
Sat & Sun: 08:00 – 22:00
Style & Branding:
The design must match the visual identity of Haulport 41Ter
Please refer to the attached photos of existing parking signage for guidance on colors, typography, and layout style
Our logo (attached) must be clearly visible and professionally integrated
Feel free to use icons or pictograms to visually support the message (e.g., ticket, truck, arrow)
Readability is key – large, bold text and high contrast colors that are visible from a distance
Target Audience:
International truck drivers – people who need fast, clear communication. Not everyone speaks the local language, so visual clarity and multilingual messaging are critical.
File Requirements:
Print-ready file (PDF or EPS) – 300 dpi at 1:10 scale
Include 5 cm bleed on all sides
Provide open source files if possible (AI or PSD)

```html
<!DOCTYPE html>
<html lang="en">
<head>
<meta charset="utf-8">
<title>Haulport 41Ter – Ticket Validation Parking Banner</title>
<link href="https://fonts.googleapis.com/css2?family=Roboto+Condensed:ital,wght@0,400;0,500;0,700;1,700&display=swap" rel="stylesheet">
<style>
  :root {
    --navy: #2b2d5f;
    --navy-light: #35386c;
    --brand-blue: #1f6fc0;
    --panel-blue: #2172b8;
    --ink-navy: #262a5a;
    --white: #ffffff;
    --alert-red: #d9232e;
    --page: #e8edf2;
  }
  * { margin: 0; padding: 0; box-sizing: border-box; }
  html, body { width: 1200px; height: 780px; overflow: hidden; }
  body { background: var(--page); font-family: "Roboto Condensed", sans-serif; position: relative; }

  .banner {
    position: absolute; left: 30px; top: 230px;
    width: 1140px; height: 320px;
    background: var(--navy); overflow: hidden; color: var(--white);
  }
  .banner-shapes { position: absolute; inset: 0; }

  .headline { position: absolute; left: 28px; font-weight: 700; text-transform: uppercase; white-space: nowrap; line-height: 1; }
  .headline-1 { top: 34px; font-size: 36px; }
  .headline-2 { top: 80px; font-size: 36px; }
  .headline-3 { top: 124px; font-size: 50px; }
  .highlight { background: var(--brand-blue); padding: 0 6px 0 4px; }

  .hours-title {
    position: absolute; left: 28px; top: 176px;
    font-size: 35px; font-weight: 700; line-height: 44px; color: var(--ink-navy); text-transform: uppercase;
  }
  .hours-arrow { position: absolute; left: 193px; font-size: 20px; font-weight: 500; letter-spacing: -3px; }
  .hours-text { position: absolute; left: 233px; font-size: 20px; font-weight: 400; line-height: 28px; }

  .attention {
    position: absolute; left: 548px; top: 44px;
    font-size: 30px; font-weight: 700; font-style: italic; line-height: 36px; text-transform: uppercase;
  }
  .parking-p { position: absolute; left: 760px; top: 38px; font-size: 70px; font-weight: 500; line-height: 1; }
  .parking-divider { position: absolute; left: 812px; top: 50px; width: 2px; height: 54px; background: var(--white); }
  .parking-label { position: absolute; left: 826px; top: 46px; font-weight: 700; text-transform: uppercase; line-height: 1; }
  .parking-label span { display: block; }
  .parking-label .small { font-size: 19px; letter-spacing: 2px; }
  .parking-label .large { font-size: 34px; letter-spacing: 2px; margin-top: 4px; }
  .alert-rule { position: absolute; left: 530px; top: 118px; width: 520px; height: 3px; background: var(--alert-red); }

  .brand-name {
    position: absolute; left: 930px; top: 54px;
    font-size: 34px; font-weight: 700; color: var(--white); line-height: 1; white-space: nowrap;
  }

  .languages { position: absolute; left: 455px; top: 130px; list-style: none; }
  .languages li { display: flex; align-items: center; height: 31px; font-size: 15.5px; font-weight: 500; white-space: nowrap; }
  .languages svg { width: 22px; height: 22px; margin-right: 13px; flex: none; }
</style>
</head>
<body>
<section class="banner" aria-label="Ticket validation parking banner">
  <svg class="banner-shapes" width="1140" height="320" viewBox="0 0 1140 320" aria-hidden="true">
    <polygon points="575,0 1140,0 1140,300" fill="var(--navy-light)"/>
    <polygon points="0,138 478,320 0,320" fill="var(--panel-blue)"/>
    <polygon points="556,42 756,42 738,118 538,118" fill="var(--brand-blue)"/>
  </svg>

  <h1>
    <span class="headline headline-1"><span class="highlight">Kindly ensure</span> ticket</span>
    <span class="headline headline-2">Validation inside the shop</span>
    <span class="headline headline-3">Before <span class="highlight">Parking</span></span>
  </h1>

  <p class="hours-title">Shop<br>Opening<br>Hours.</p>
  <span class="hours-arrow" style="top:192px">&gt;&gt;</span>
  <p class="hours-text" style="top:180px">Sat &amp; Sun:<br>08:00 – 22:00</p>
  <span class="hours-arrow" style="top:250px">&gt;&gt;</span>
  <p class="hours-text" style="top:238px">Mon – Fri:<br>05:30 – 22:00</p>

  <p class="attention">Attention<br>required for</p>
  <span class="parking-p">P</span>
  <span class="parking-divider"></span>
  <p class="parking-label"><span class="small">Parking</span><span class="large">Area</span></p>
  <span class="alert-rule"></span>

  <p class="brand-name">Haulport 41Ter</p>

  <ul class="languages">
    <li><svg viewBox="0 0 20 20"><clipPath id="c-nl"><circle cx="10" cy="10" r="10"/></clipPath><g clip-path="url(#c-nl)"><rect width="20" height="7" fill="#c8102e"/><rect y="7" width="20" height="6" fill="#fff"/><rect y="13" width="20" height="7" fill="#21468b"/></g></svg>Vergeet je ticket niet te valideren in de shop – verplicht, ook bij kort parkeren!</li>
    <li><svg viewBox="0 0 20 20"><clipPath id="c-fr"><circle cx="10" cy="10" r="10"/></clipPath><g clip-path="url(#c-fr)"><rect width="7" height="20" fill="#0055a4"/><rect x="7" width="6" height="20" fill="#fff"/><rect x="13" width="7" height="20" fill="#ef4135"/></g></svg>N'oubliez pas de valider votre ticket à la boutique – obligatoire, même pour un court arrêt !</li>
    <li><svg viewBox="0 0 20 20"><clipPath id="c-en"><circle cx="10" cy="10" r="10"/></clipPath><g clip-path="url(#c-en)"><rect width="20" height="20" fill="#012169"/><path d="M0 0L20 20M20 0L0 20" stroke="#fff" stroke-width="4"/><path d="M0 0L20 20M20 0L0 20" stroke="#c8102e" stroke-width="1.5"/><path d="M10 0V20M0 10H20" stroke="#fff" stroke-width="6"/><path d="M10 0V20M0 10H20" stroke="#c8102e" stroke-width="3"/></g></svg>Don't forget to validate your entry ticket in the shop – mandatory, even for short stops!</li>
    <li><svg viewBox="0 0 20 20"><clipPath id="c-de"><circle cx="10" cy="10" r="10"/></clipPath><g clip-path="url(#c-de)"><rect width="20" height="7" fill="#000"/><rect y="7" width="20" height="6" fill="#dd0000"/><rect y="13" width="20" height="7" fill="#ffce00"/></g></svg>Vergessen Sie nicht, Ihr Einfahrticket im Shop zu entwerten – Pflicht, auch bei kurzem Parken!</li>
    <li><svg viewBox="0 0 20 20"><clipPath id="c-pl"><circle cx="10" cy="10" r="10"/></clipPath><g clip-path="url(#c-pl)"><rect width="20" height="10" fill="#fff"/><rect y="10" width="20" height="10" fill="#dc143c"/></g></svg>Nie zapomnij zatwierdzić biletu w sklepie – obowiązkowe, nawet przy krótkim postoju!</li>
    <li><svg viewBox="0 0 20 20"><clipPath id="c-ro"><circle cx="10" cy="10" r="10"/></clipPath><g clip-path="url(#c-ro)"><rect width="7" height="20" fill="#002b7f"/><rect x="7" width="6" height="20" fill="#fcd116"/><rect x="13" width="7" height="20" fill="#ce1126"/></g></svg>Nu uitați să validați biletul în magazin – obligatoriu, chiar și pentru opriri scurte!</li>
  </ul>
</section>
</body>
</html>
```